Business card design

I already have the logo design completed and am requiring business card design and layout utilising the logo. I require a front and back design.

We are an executive recruitment company so we are looking at full colour, high finish in a reasonably conservative structure.

Reason: will be provide ai template

Target Market(s)

Senior Management 35-60 age bracket

Industry/Entity Type

Business

Requirements
Must have
• Peter Welling
• Director
• 238 Morrow Tce, Kelvin Grove QLD 4059
• Ph: 07 3628 4190 Mob: 0418527306
• peter@voltinapartners.com.au
• www.voltinapartners.com.au
Nice to have
• Ideally full colour,
Should not have
• cheap looking

```html
<!DOCTYPE html>
<html lang="en">
<head>
<meta charset="utf-8">
<title>Voltina Partners – Business Card</title>
<link rel="stylesheet" href="https://fonts.googleapis.com/css2?family=Source+Sans+3:wght@400;600;700&display=swap">
<style>
  :root {
    --navy: #123b6c;
    --blue-light: #2173a8;
    --blue-deep: #0c3a68;
    --edge-blue: #0e4a80;
    --text-grey: #a6a6a6;
    --title-grey: #5c5c5c;
    --card-white: #ffffff;
    --backdrop: #e6e7e9;
    --edge-silver: #c9cdd2;
  }
  * { box-sizing: border-box; margin: 0; padding: 0; }
  html, body {
    width: 1200px;
    height: 1200px;
    overflow: hidden;
    background: var(--backdrop);
    font-family: "Source Sans 3", "Myriad Pro", Arial, sans-serif;
  }
  .canvas {
    position: relative;
    width: 1200px;
    height: 1200px;
  }
  .card {
    position: absolute;
    left: 160px;
    width: 880px;
    height: 520px;
    box-shadow: 0 6px 22px rgba(0, 0, 0, 0.18);
    overflow: hidden;
  }
  .card-front {
    top: 50px;
    background: var(--card-white);
  }
  .card-front::after {
    content: "";
    position: absolute;
    top: 0;
    right: 0;
    width: 14px;
    height: 100%;
    background: var(--edge-blue);
  }
  .brand {
    position: absolute;
    left: 76px;
    top: 82px;
    display: flex;
    align-items: center;
    gap: 22px;
  }
  .brand-square {
    width: 78px;
    height: 78px;
    background: var(--navy);
  }
  .brand-name {
    font-weight: 700;
    font-size: 46px;
    letter-spacing: 2px;
    color: var(--navy);
    line-height: 1;
  }
  .person {
    position: absolute;
    left: 72px;
    top: 282px;
  }
  .person-name {
    font-weight: 700;
    font-size: 36px;
    color: var(--navy);
    line-height: 1.1;
  }
  .person-title {
    font-weight: 400;
    font-size: 29px;
    letter-spacing: 1px;
    color: var(--title-grey);
    line-height: 1.3;
  }
  .contact {
    position: absolute;
    left: 482px;
    top: 280px;
    font-size: 25px;
    line-height: 41px;
    color: var(--text-grey);
    list-style: none;
  }
  .card-back {
    top: 630px;
    background: linear-gradient(160deg, var(--blue-light) 0%, var(--blue-deep) 100%);
  }
  .card-back::after {
    content: "";
    position: absolute;
    top: 0;
    right: 0;
    width: 14px;
    height: 100%;
    background: var(--edge-silver);
  }
</style>
</head>
<body>
<main class="canvas">
  <section class="card card-front" aria-label="Business card front">
    <div class="brand">
      <span class="brand-square"></span>
      <span class="brand-name">VOLTINA PARTNERS</span>
    </div>
    <div class="person">
      <p class="person-name">Peter Welling</p>
      <p class="person-title">Director</p>
    </div>
    <ul class="contact">
      <li>238 Morrow Tce, Kelvin Grove</li>
      <li>QLD 4059</li>
      <li>P: 07 3628 4190</li>
      <li>M: 0418 527 306</li>
      <li>peter@voltinapartners.com.au</li>
    </ul>
  </section>
  <section class="card card-back" aria-label="Business card back, deep blue gradient"></section>
</main>
</body>
</html>
```